Values and Organizational Purpose Signage

We recently solidified our company values, organizatioanal purpose and strategic vision. I'd like to develop some tasteful (not overly corporate) signage of these values to display in our office.

I've attached the hand-written values and purpose that my core team members then initialed acknowleding they align along with the signage at the front of our office to provide some perspective on our brand identity.

Industry/Entity Type

It Company

Font styles to use
Sans Serif

Requirements
Must have
• I'd like to see the values and org purpose depicted as one sign and as separate signs (i.e., values on one sign and org purpose on another). I need it to reflect our brand identity which I've uploaded

```html
<!DOCTYPE html>
<html lang="en">
<head>
<meta charset="utf-8">
<title>Organizational Purpose and Core Values Signage</title>
<link rel="stylesheet" href="https://fonts.googleapis.com/css2?family=Jost:wght@400;500;700&display=swap">
<style>
  :root {
    --backdrop: #eef0ea;
    --frame: #ffffff;
    --panel: #022f33;
    --accent: #7c9b1f;
    --accent-text: #95ad3c;
    --pin: #0b2b2d;
  }
  * { box-sizing: border-box; margin: 0; padding: 0; }
  html, body { width: 1200px; height: 748px; overflow: hidden; }
  body {
    background: var(--backdrop);
    font-family: "Jost", sans-serif;
    position: relative;
  }
  .sign {
    position: absolute;
    left: 385px;
    width: 430px;
    background: var(--frame);
    box-shadow: 0 3px 10px rgba(0,0,0,0.18);
  }
  .sign--purpose { top: 160px; height: 147px; }
  .sign--values { top: 367px; height: 295px; }
  .pin {
    position: absolute;
    width: 6px; height: 6px;
    border-radius: 50%;
    background: var(--pin);
  }
  .pin--tl { top: 5px; left: 5px; }
  .pin--tr { top: 5px; right: 5px; }
  .pin--bl { bottom: 5px; left: 5px; }
  .pin--br { bottom: 5px; right: 5px; }
  .panel {
    position: absolute;
    top: 13px; left: 13px; right: 13px; bottom: 13px;
    background: var(--panel);
  }
  .sign__title {
    position: absolute;
    font-weight: 700;
    color: var(--accent);
    letter-spacing: 0.5px;
    line-height: 1;
  }
  .sign--purpose .sign__title { left: 20px; top: 16px; font-size: 25px; }
  .rule {
    position: absolute;
    left: 20px;
    width: 360px;
    height: 5px;
    background: var(--accent);
  }
  .purpose__text {
    position: absolute;
    left: 23px; top: 62px;
    font-size: 19.5px;
    line-height: 24px;
    color: var(--accent-text);
  }
  .sign--values .sign__title {
    left: 0; right: 0; top: 18px;
    text-align: center;
    font-size: 25px;
  }
  .value {
    position: absolute;
    left: 20px;
    width: 360px;
    display: flex;
    align-items: center;
  }
  .value__name {
    width: 152px;
    font-weight: 700;
    font-size: 16.5px;
    line-height: 18px;
    color: var(--accent);
    letter-spacing: 0.3px;
  }
  .value__text {
    flex: 1;
    font-size: 11.5px;
    line-height: 14.5px;
    color: var(--accent-text);
  }
</style>
</head>
<body>
  <section class="sign sign--purpose">
    <span class="pin pin--tl"></span><span class="pin pin--tr"></span>
    <span class="pin pin--bl"></span><span class="pin pin--br"></span>
    <div class="panel">
      <h1 class="sign__title">ORGANIZATIONAL PURPOSE</h1>
      <div class="rule" style="top:49px"></div>
      <p class="purpose__text">We deliver simple and digestible<br>solutions to complex matters</p>
    </div>
  </section>

  <section class="sign sign--values">
    <span class="pin pin--tl"></span><span class="pin pin--tr"></span>
    <span class="pin pin--bl"></span><span class="pin pin--br"></span>
    <div class="panel">
      <h2 class="sign__title">CORE VALUES DEFINED</h2>
      <div class="value" style="top:56px;height:32px">
        <span class="value__name">RESPECT</span>
        <span class="value__text">We are transparent and receptive to the thoughts, opinion and feelings of others</span>
      </div>
      <div class="rule" style="top:90px"></div>
      <div class="value" style="top:106px;height:30px;align-items:flex-start">
        <span class="value__name" style="padding-top:5px">INTEGRITY</span>
        <span class="value__text" style="padding-top:2px">We uphold our promises</span>
      </div>
      <div class="rule" style="top:139px"></div>
      <div class="value" style="top:153px;height:32px">
        <span class="value__name">EXCELLENCE</span>
        <span class="value__text">We continuously strive to be the best in all endeavors</span>
      </div>
      <div class="rule" style="top:189px"></div>
      <div class="value" style="top:206px;height:38px;align-items:flex-start">
        <span class="value__name">OPEN<br>MINDEDNESS</span>
        <span class="value__text">We encourage creative and innovative expressions</span>
      </div>
    </div>
  </section>
</body>
</html>
```